Local Flower Farm Needs Business Card Design

I need business cards designed for a flower farm based in Eudora, Kansas.
Business Info:
We are a local cut flower farm located in Eudora, Kansas, founded by Corinne Haldwick. What started as a passion for agriculture and search for more joy in daily life has blossomed into a small business dedicated to providing the community with beautiful, fresh, and sustainable flowers. We specialize in local, seasonal blooms, ensuring that every petal reflects the care and dedication we pour into our craft. Our mission is to deliver the highest quality flowers directly to our customers through local farmers markets and to florists who share our commitment to sustainability. Join us in celebrating the beauty of nature, one bloom at a time!
Contact Details:
Corinne Haldwick
Owner
Phone 913-555-0147
Facebook: Rosalind Thorpe Gardens
Instagram: @RosalindThorpeGardens
Website: RosalindThorpeGardens.example
Target Market(s)
Wholesale to Florists and Direct to Consumer via Farmers Market
Industry/Entity Type
Florist, Farm
Contact Information for Business Card
Name, Contact Info, Logo
Look and feel
Each slider illustrates characteristics of the customer's brand and the style your logo design should communicate.

```html
<!DOCTYPE html>
<html lang="en">
<head>
<meta charset="utf-8">
<title>Rosalind Thorpe Gardens – Business Card</title>
<link href="https://fonts.googleapis.com/css2?family=Montserrat:wght@400;500;700&display=swap" rel="stylesheet">
<style>
  :root {
    --page: #e9e6e1;
    --card-light: #ffffff;
    --card-dark: #0b2a2e;
    --ink: #0f2b2f;
    --ink-soft: #1d1d1d;
    --faint: #e4e4e4;
    --on-dark: #ffffff;
  }
  * { margin: 0; padding: 0; box-sizing: border-box; }
  html, body { width: 900px; height: 1200px; overflow: hidden; }
  body {
    background: var(--page);
    position: relative;
    font-family: "Montserrat", sans-serif;
    color: var(--ink-soft);
  }
  .card {
    position: absolute;
    border-radius: 22px;
    overflow: hidden;
  }
  .card-front {
    left: 80px; top: 131px; width: 742px; height: 440px;
    background: var(--card-light);
  }
  .card-back {
    left: 78px; top: 640px; width: 744px; height: 438px;
    background: var(--card-dark);
  }
  .brand-seal {
    position: absolute;
    border-radius: 50%;
    display: flex; align-items: center; justify-content: center;
    text-align: center;
    font-family: "Montserrat", sans-serif;
    font-weight: 500;
    letter-spacing: 0.14em;
    text-transform: uppercase;
    line-height: 1.35;
  }
  .card-front .brand-seal {
    left: 36px; top: 49px; width: 224px; height: 224px;
    border: 1.5px solid var(--ink);
    color: var(--ink);
    font-size: 17px;
  }
  .card-back .brand-seal {
    left: 216px; top: 64px; width: 312px; height: 312px;
    border: 1.5px solid var(--on-dark);
    color: var(--on-dark);
    font-size: 24px;
  }
  .brand-mark-faint {
    position: absolute;
    left: 470px; top: 190px; width: 230px; height: 240px;
    display: flex; align-items: center; justify-content: center;
    text-align: center;
    color: var(--faint);
    font-weight: 500;
    font-size: 30px;
    line-height: 1.2;
    letter-spacing: 0.06em;
    text-transform: uppercase;
  }
  .holder {
    position: absolute;
    right: 50px; top: 44px;
    text-align: right;
  }
  .holder-name {
    font-weight: 700;
    font-size: 27px;
    color: var(--ink);
    letter-spacing: 0.01em;
  }
  .holder-role {
    font-weight: 400;
    font-size: 16px;
    margin-top: 2px;
  }
  .contact-list {
    position: absolute;
    left: 38px; top: 306px;
    list-style: none;
  }
  .contact-item {
    display: flex; align-items: center;
    font-size: 16px;
    height: 26px;
  }
  .contact-icon {
    width: 14px; height: 14px;
    margin-right: 10px;
    flex: none;
  }
  .dot-icon {
    width: 13px; height: 13px;
    border-radius: 50%;
    background: var(--ink-soft);
    margin-right: 11px;
    flex: none;
  }
</style>
</head>
<body>

<section class="card card-front">
  <div class="brand-seal">Rosalind<br>Thorpe<br>Gardens</div>

  <div class="holder">
    <div class="holder-name">Corinne Haldwick</div>
    <div class="holder-role">Owner</div>
  </div>

  <div class="brand-mark-faint" aria-hidden="true">Rosalind<br>Thorpe<br>Gardens</div>

  <ul class="contact-list">
    <li class="contact-item">
      <svg class="contact-icon" viewBox="0 0 24 24" aria-hidden="true">
        <path d="M6.6 10.8a15 15 0 0 0 6.6 6.6l2.2-2.2a1 1 0 0 1 1-.25 11.4 11.4 0 0 0 3.6.6 1 1 0 0 1 1 1V20a1 1 0 0 1-1 1A17 17 0 0 1 3 4a1 1 0 0 1 1-1h3.5a1 1 0 0 1 1 1c0 1.25.2 2.45.6 3.6a1 1 0 0 1-.25 1z" fill="none" stroke="#1d1d1d" stroke-width="2"/>
      </svg>
      913-555-0147
    </li>
    <li class="contact-item"><span class="dot-icon"></span>Rosalind Thorpe Gardens</li>
    <li class="contact-item"><span class="dot-icon"></span>@RosalindThorpeGardens</li>
    <li class="contact-item">
      <svg class="contact-icon" viewBox="0 0 24 24" aria-hidden="true">
        <circle cx="12" cy="12" r="10" fill="none" stroke="#1d1d1d" stroke-width="2"/>
        <ellipse cx="12" cy="12" rx="4.5" ry="10" fill="none" stroke="#1d1d1d" stroke-width="1.6"/>
        <line x1="2" y1="12" x2="22" y2="12" stroke="#1d1d1d" stroke-width="1.6"/>
      </svg>
      www.RosalindThorpeGardens.example
    </li>
  </ul>
</section>

<section class="card card-back">
  <div class="brand-seal">Rosalind<br>Thorpe<br>Gardens</div>
</section>

</body>
</html>
```